Coastal Learner Bureau business cards

Australian company about to start offering its services. We recruit international students to come to study English, vocational education and postgraduate courses in Australia. We help them find the institution and select the right city they want to come to Australia. We are a young, online oriented and supportive agency. Our clients are between 18 and 35 years old, mainly University students, young professionals or people with work experience. We provide much more information that any other agency offer. We administrate a Facebook group with more than 11.000 members that daily ask questions about general information when coming to Australia, while they are here and even after they leave the country

Target Market(s)

International students from South America, Central America and Europe

Industry/Entity Type

Student

Contact Information for Business Card

Tomas Bilbrea
Managing Director
tomas@kelvarin.com.au
www.kelvoria.com.au
+61 491058264
Wrenhaven, Victoria

Font styles to use
Serif
Sans Serif

Colors

Designer to choose colors to be used in the design.

Requirements
Must have
• Horizontal design
• Standard business card size and shape. If font uses green or yellow colours, they will have to match the ones from the logo
Nice to have
• UPDATE: Use the contents of the green image to design one of the card sides. Use our logo in the background of that side as watermark.
• Passport image, or immigration stamps. A picture of the Yarra River (from Melbourne) would be cool as well.
Should not have
• Non-standard business card size and shape
• Not black as the background colour of any sides as we are not a VIP agency or a hight class service. We are orientes to young people and they like colours, pictures, something attractive.
• Vertical design
• NO YELLOW or BLACK AS THE BACKGROUND COLOUR OF ANY SIDE OF THE BIZ CARD

```html
<!DOCTYPE html>
<html lang="en">
<head>
<meta charset="utf-8">
<title>Coastal Learner Bureau — Business Cards</title>
<link href="https://fonts.googleapis.com/css2?family=Jost:wght@400;500;600;700&display=swap" rel="stylesheet">
<style>
  :root {
    --backdrop: #8e8d8e;
    --card: #ffffff;
    --green: #1a5e3a;
    --yellow: #e2b822;
    --ink: #2b2b2b;
    --muted: #3d3d3d;
  }
  * { box-sizing: border-box; margin: 0; padding: 0; }
  html, body {
    width: 1200px; height: 929px; overflow: hidden;
    background: var(--backdrop);
    font-family: "Jost", sans-serif;
  }
  .stage { position: relative; width: 1200px; height: 929px; }
  .card {
    position: absolute; left: 280px;
    width: 640px; height: 366px;
    background: var(--card);
    box-shadow: 0 8px 22px rgba(0,0,0,0.25);
  }
  .card--front { top: 70px; }
  .card--back { top: 493px; }

  .brand {
    display: flex; align-items: center; gap: 10px;
    color: var(--green);
    font-weight: 600;
    font-size: 52px;
    letter-spacing: 0.5px;
    white-space: nowrap;
  }
  .brand__dot {
    width: 22px; height: 22px; border-radius: 50%;
    background: var(--yellow);
  }
  .card--front .brand {
    position: absolute; left: 0; right: 0; top: 136px;
    justify-content: center;
  }
  .tagline {
    position: absolute; left: 0; right: 0; bottom: 58px;
    text-align: center;
    font-size: 15px; font-weight: 500; color: var(--ink);
    letter-spacing: 0.6px;
  }
  .card--back .brand {
    position: absolute; left: 48px; top: 150px;
    font-size: 48px;
  }
  .divider {
    position: absolute; left: 340px; top: 92px;
    width: 2px; height: 190px; background: var(--green);
  }
  .contact { position: absolute; left: 366px; top: 96px; }
  .contact__name {
    color: var(--green); font-weight: 700; font-size: 27px;
    letter-spacing: 1px; line-height: 1.05; white-space: nowrap;
  }
  .contact__role {
    color: var(--muted); font-size: 18px; font-weight: 400;
    letter-spacing: 0.6px; margin-top: 2px;
  }
  .contact__list { list-style: none; margin-top: 24px; }
  .contact__item {
    display: flex; align-items: center; gap: 12px;
    font-size: 16px; color: var(--ink); letter-spacing: 0.5px;
    line-height: 25px; white-space: nowrap;
  }
  .contact__icon { width: 14px; height: 14px; flex: none; }
</style>
</head>
<body>
<main class="stage">
  <section class="card card--front" aria-label="Card front">
    <div class="brand"><span class="brand__dot"></span>Kelvoria</div>
    <p class="tagline">Contigo en cada paso!</p>
  </section>

  <section class="card card--back" aria-label="Card back">
    <div class="brand"><span class="brand__dot"></span>Kelvoria</div>
    <div class="divider"></div>
    <div class="contact">
      <h1 class="contact__name">TOMAS BILBREA</h1>
      <p class="contact__role">Managing Director</p>
      <ul class="contact__list">
        <li class="contact__item">
          <svg class="contact__icon" viewBox="0 0 14 14"><rect x="3.5" y="1" width="7" height="12" rx="1.2" fill="none" stroke="#1a5e3a" stroke-width="1.4"/></svg>
          +61 491058264
        </li>
        <li class="contact__item">
          <svg class="contact__icon" viewBox="0 0 14 14"><rect x="1" y="3" width="12" height="8.5" fill="#1a5e3a"/><path d="M1.5 3.5 L7 8 L12.5 3.5" fill="none" stroke="#fff" stroke-width="1.2"/></svg>
          tomas@kelvarin.com.au
        </li>
        <li class="contact__item">
          <svg class="contact__icon" viewBox="0 0 14 14"><circle cx="6" cy="6" r="4" fill="none" stroke="#1a5e3a" stroke-width="1.8"/><path d="M9 9 L13 13" stroke="#1a5e3a" stroke-width="2"/></svg>
          www.kelvoria.com.au
        </li>
        <li class="contact__item">
          <svg class="contact__icon" viewBox="0 0 14 14"><path d="M7 13 C3 8 2.5 6.5 2.5 5 A4.5 4.5 0 0 1 11.5 5 C11.5 6.5 11 8 7 13 Z" fill="#1a5e3a"/><circle cx="7" cy="5" r="1.6" fill="#fff"/></svg>
          Wrenhaven, Victoria
        </li>
      </ul>
    </div>
  </section>
</main>
</body>
</html>
```